Non Profit Company Looking For New Website

The website for Fernvale Quillstone Heritage Society should offer the viewer beautiful photos that inspire condifence and joy and tap into our love of horses.

We would like to see a website that displays trust, quality and confidence. Needs to be responsive and mobile friendly for all browsers and coded for both Android & IOS.

READ ATTACHED WEBSITE TEMPLATE FOR COMPLETE DETAILS ON WHAT WE ARE LOOKING FOR.

Looking for recommmendations if we should use WordPress/WooCommerce for site or Wordpress with Shopify Plug in or just Shopify.

Must be both desktop and mobile friendly with fast page load speed. Need the ability to edit ourselves.

Industry/Entity Type

Non Profit

Coding

Coded - Design and coding required

Number of Pages Required

5+ page

Requirements
Must have
• We would like to see a website that displays trust, quality and confidence. Needs to be responsive and mobile friendly for all browsers and coded for both Android & IOS.

Looking for recommendations if we should use WordPress/WooCommerce for site or Wordpress with Shopify Plug in or just Shopify.

Logo Colour:
Pantone 7621 C

READ TEMPLATE THAT IS ATTACHED
Nice to have
• Like look of this website as a sample:
https://www.quellbrimtorva.com/

Another similar non profit organization
https://pellaworthcindle.com/

```html
<!DOCTYPE html>
<html lang="en">
<head>
<meta charset="utf-8">
<title>Fernvale Quillstone Heritage Society — Website Design</title>
<link href="https://fonts.googleapis.com/css2?family=Gilda+Display&family=Montserrat:wght@400;500;600&display=swap" rel="stylesheet">
<style>
:root{
  --red:#bd1f2d;
  --red-dark:#9a1722;
  --red-bright:#e0303c;
  --ink:#1c1c1c;
  --charcoal:#262626;
  --black:#0b0b0b;
  --white:#ffffff;
  --paper:#f3f3f3;
  --ghost:#e2e2e2;
  --serif:'Gilda Display', Georgia, serif;
  --sans:'Montserrat', Arial, sans-serif;

  /* photo tone fills */
  --arena:
    radial-gradient(ellipse 22% 34% at 72% 22%, rgba(236,180,140,.85), rgba(236,180,140,0) 70%),
    radial-gradient(ellipse 18% 26% at 90% 30%, rgba(214,150,110,.7), rgba(214,150,110,0) 70%),
    radial-gradient(ellipse 26% 40% at 64% 68%, rgba(14,9,7,.95), rgba(14,9,7,0) 72%),
    radial-gradient(ellipse 40% 20% at 70% 98%, rgba(120,80,60,.7), rgba(120,80,60,0) 70%),
    linear-gradient(90deg,#040303 0%,#120c0a 22%,#3e281e 45%,#8a5a44 70%,#b07a5c 84%,#5a3a2c 100%);
  --portrait:
    radial-gradient(circle at 62% 30%, rgba(214,160,120,.9), rgba(214,160,120,0) 40%),
    radial-gradient(circle at 35% 62%, #6e3f26, rgba(110,63,38,0) 55%),
    radial-gradient(circle at 30% 80%, rgba(25,14,9,.9), rgba(25,14,9,0) 50%),
    linear-gradient(135deg,#caa98a 0%,#8a5634 45%,#3a2214 100%);
  --bay-halter:
    radial-gradient(ellipse 30% 45% at 40% 50%, #5a2c1a, rgba(90,44,26,0) 75%),
    radial-gradient(ellipse 10% 8% at 48% 66%, rgba(206,58,80,.8), rgba(206,58,80,0) 80%),
    radial-gradient(ellipse 30% 55% at 85% 40%, rgba(236,214,190,.9), rgba(236,214,190,0) 75%),
    linear-gradient(120deg,#d8c6b2 0%,#7a4630 45%,#3a1e12 75%,#a48870 100%);
  --paddock:
    radial-gradient(ellipse 28% 38% at 45% 55%, #3a2214, rgba(58,34,20,0) 75%),
    linear-gradient(180deg,#e9ede4 0%,#c7cfbd 40%,#8b9a6e 62%,#6a7a4a 100%);
  --snow:
    radial-gradient(ellipse 30% 40% at 50% 52%, #2e1a10, rgba(46,26,16,0) 75%),
    linear-gradient(180deg,#d8dde2 0%,#b8c0c8 35%,#eef1f4 62%,#ffffff 100%);
  --field:
    radial-gradient(ellipse 28% 36% at 50% 55%, #5a3418, rgba(90,52,24,0) 75%),
    linear-gradient(180deg,#efe28a 0%,#d9c84e 45%,#b8a33a 75%,#8c7b2a 100%);
  --art:
    radial-gradient(ellipse 14% 30% at 30% 40%, #ffffff, rgba(255,255,255,0) 80%),
    radial-gradient(ellipse 14% 22% at 70% 30%, rgba(120,70,50,.35), rgba(120,70,50,0) 80%),
    radial-gradient(ellipse 20% 40% at 52% 60%, rgba(189,31,45,.55), rgba(189,31,45,0) 80%),
    linear-gradient(180deg,#fafafa,#eeeeee);
}
*{box-sizing:border-box;margin:0;padding:0}
html,body{width:1200px;height:4341px;overflow:hidden}
body{background:var(--paper);font-family:var(--sans);color:var(--ink);position:relative}
.board-label{position:absolute;font-weight:400;font-size:36px;color:var(--ink);text-align:center;line-height:1.1}
.label-desktop{left:40px;top:40px;width:780px}
.label-mobile{left:880px;top:20px;width:280px}
.closing{position:absolute;left:60px;top:2760px;font-weight:600;font-size:110px;line-height:1.05;color:var(--ghost);letter-spacing:2px}

.photo{display:block}
.btn{display:inline-block;font-family:var(--serif);text-transform:uppercase;letter-spacing:.5px;background:var(--white);color:var(--ink);white-space:nowrap}
.brand{font-family:var(--serif);color:var(--red);text-transform:uppercase;text-align:center;line-height:1.15}

/* ---------- desktop ---------- */
.desktop{position:absolute;left:40px;top:110px;width:780px;background:var(--white);box-shadow:0 6px 24px rgba(0,0,0,.18)}
.d-nav{height:81px;position:relative}
.d-nav .brand{position:absolute;left:90px;top:22px;font-size:11px;width:110px}
.d-menu{position:absolute;left:301px;width:383px;top:36px;display:flex;justify-content:space-between;font-size:8px;font-weight:500;letter-spacing:.4px}
.d-menu .active{color:var(--red)}
.d-hero{height:350px;position:relative;background:var(--arena)}
.d-hero-copy{position:absolute;left:89px;top:86px;color:var(--white);font-family:var(--serif)}
.d-hero-copy .l1{font-size:21px}
.d-hero-copy .l2{font-size:26px;color:var(--red-bright)}
.d-hero-copy p{font-size:15px;line-height:1.45;width:215px;margin-top:2px}
.d-hero-copy .btn{font-size:9px;padding:7px 26px;margin-top:14px}
.d-intro{height:315px;text-align:center;padding-top:20px}
.art{margin:0 auto;position:relative;background:var(--art)}
.art .tag{position:absolute;left:0;right:0;font-family:var(--serif);font-style:italic;color:var(--red)}
.d-intro .art{width:269px;height:175px}
.d-intro .art .tag{font-size:16px;bottom:40px}
.d-intro p{font-size:9.5px;line-height:1.6;color:#444;margin-top:28px}
.d-what{height:323px;background:linear-gradient(90deg,var(--red),var(--red-dark));position:relative;color:var(--white)}
.d-what .copy{position:absolute;left:89px;top:72px}
.d-what h2{font-family:var(--serif);font-weight:400;font-size:17px;line-height:1.3}
.d-what p{font-size:7.5px;line-height:1.7;width:265px;margin-top:14px}
.d-what .btn{font-size:7px;padding:5px 9px;margin-top:14px}
.d-what .circle{position:absolute;left:427px;top:38px;width:256px;height:256px;border-radius:50%;background:var(--portrait)}
.d-adopt{height:444px;background:var(--charcoal);text-align:center;color:var(--white);padding-top:66px}
.d-adopt h2{font-family:var(--serif);font-weight:400;font-size:18px}
.d-adopt p{font-size:7.5px;line-height:1.6;margin-top:8px}
.horse-row{display:flex;justify-content:center;gap:11px;margin-top:24px}
.horse-row .photo{width:188px;height:175px;border:2px solid #d22e3a}
.d-adopt .btn{font-size:7px;padding:6px 26px;margin-top:26px}
.d-horses{height:412px;position:relative}
.d-horses .photo{position:absolute;left:89px;top:40px;width:492px;height:344px;background:var(--bay-halter)}
.d-horses .card{position:absolute;left:347px;top:89px;width:336px;height:247px;background:var(--red);color:var(--white);padding:60px 42px 0 42px}
.card h3{font-family:var(--serif);font-weight:400;font-size:14px}
.d-horses .card p{font-size:8px;line-height:1.7;margin-top:12px}
.card .btn{font-size:7px;padding:5px 9px;margin-top:14px}
.d-contact{height:323px;background:linear-gradient(90deg,var(--red),var(--red-dark));color:var(--white);position:relative}
.d-contact h2{position:absolute;left:0;right:0;top:40px;font-family:var(--serif);font-weight:400;font-size:17px;text-align:center}
.d-info{position:absolute;left:89px;top:96px}
.info-row{display:flex;align-items:flex-start;gap:10px}
.info-row svg{flex:none}
.d-info .info-row{margin-bottom:22px}
.d-info b{display:block;font-size:7px;font-weight:600}
.d-info span{font-size:6.5px;line-height:1.5;display:block;margin-top:2px}
.d-form{position:absolute;left:342px;top:98px;width:342px;display:grid;grid-template-columns:1fr 1fr;gap:8px}
.field{background:var(--white);color:#777;font-size:7px;padding:5px 7px;height:22px}
.d-form .wide{grid-column:1/3;height:72px}
.d-form .foot{grid-column:1/3;display:flex;gap:8px}
.d-form .check{width:130px;height:22px;background:var(--white)}
.d-form .submit{width:130px;height:22px;background:var(--white);color:var(--ink);font-family:var(--serif);font-size:7px;text-align:center;line-height:22px}
.d-footer{height:274px;background:var(--black);color:var(--white);position:relative}
.d-footer .brand{position:absolute;left:91px;top:82px;font-size:11px;width:95px}
.d-col{position:absolute;top:58px}
.d-footer h4{font-family:var(--serif);font-weight:400;font-size:7px;margin-bottom:8px}
.d-footer li{list-style:none;font-size:6px;line-height:2}
.d-footer .accent{color:var(--red)}
.sub-field{background:var(--white);color:#555;text-align:center}
.sub-btn{background:var(--red);color:var(--white);text-align:center}
.d-footer .sub-field{width:140px;height:14px;font-size:6px;line-height:14px}
.d-footer .sub-btn{width:140px;height:14px;font-size:6px;line-height:14px;margin-top:4px}
.socials{display:flex;gap:5px;margin-top:10px}
.socials i{display:block;border-radius:50%;background:var(--white)}
.d-footer .socials i{width:11px;height:11px}
.d-footer .copy{position:absolute;left:0;right:0;bottom:18px;text-align:center;font-size:5.5px;color:#888}

/* ---------- mobile ---------- */
.mobile{position:absolute;left:880px;top:110px;width:280px;background:var(--white);box-shadow:0 6px 24px rgba(0,0,0,.18);overflow:hidden;border-radius:0 0 18px 18px}
.m-head{height:60px;display:flex;align-items:center;justify-content:space-between;padding:0 14px 0 10px}
.m-head .brand{font-size:8px;width:70px}
.m-hero{height:215px;position:relative;background:var(--arena)}
.m-hero-copy{position:absolute;left:8px;top:24px;color:var(--white);font-family:var(--serif);font-size:13px;line-height:1.35}
.m-hero-copy .red{color:var(--red-bright)}
.m-hero-copy .btn{font-size:10px;padding:4px 12px;margin-top:6px}
.m-intro{height:415px;text-align:center;padding-top:40px}
.m-intro .art{width:200px;height:170px}
.m-intro .art .tag{font-size:13px;bottom:42px}
.m-intro p{font-size:12.5px;line-height:1.6;color:#444;margin-top:20px;padding:0 30px}
.m-what{height:512px;background:linear-gradient(180deg,var(--red),var(--red-dark));color:var(--white);padding:10px 8px 0}
.m-what .circle{width:175px;height:175px;border-radius:50%;margin:0 auto;background:var(--portrait);border:3px solid var(--white)}
.m-what h2{font-family:var(--serif);font-weight:400;font-size:22px;line-height:1.3;margin-top:14px}
.m-what p{font-size:12.5px;line-height:1.55;margin-top:14px}
.m-what .btn{font-size:10px;padding:3px 8px;margin-top:10px}
.m-adopt{height:512px;background:var(--charcoal);color:var(--white);padding:36px 8px 0}
.m-adopt h2{font-family:var(--serif);font-weight:400;font-size:20px}
.m-adopt p{font-size:12px;line-height:1.5;margin-top:18px}
.slider{position:relative;margin:18px auto 0;width:212px}
.slider .photo{width:212px;height:195px;border:2px solid #d22e3a;background:var(--snow)}
.slider .arrow{position:absolute;top:84px;width:24px;height:24px;border-radius:50%;background:var(--white)}
.slider .prev{left:-24px}.slider .next{right:-24px}
.m-adopt .center{text-align:center}
.m-adopt .btn{font-size:10px;padding:4px 18px;margin-top:14px}
.m-horses{padding-top:16px}
.m-horses .photo{height:220px;margin:0 2px;background:var(--bay-halter)}
.m-horses .card{height:300px;background:var(--red);color:var(--white);padding:30px 16px;margin:0 2px}
.m-horses .card h3{font-size:20px}
.m-horses .card p{font-size:12.5px;line-height:1.55;margin-top:14px}
.m-horses .card .btn{font-size:10px;padding:3px 6px;margin-top:16px}
.m-ask{height:300px;background:linear-gradient(180deg,var(--red),var(--red-dark));color:var(--white);padding:24px 6px 0;margin-top:12px}
.m-ask h2{font-family:var(--serif);font-weight:400;font-size:19px;line-height:1.35;white-space:nowrap}
.m-ask .info-list{margin-top:16px}
.m-ask .info-row{margin-bottom:16px}
.m-ask b{display:block;font-size:13px;font-weight:500}
.m-ask span{font-size:12px;line-height:1.45;display:block}
.m-form{height:330px;background:linear-gradient(180deg,#a81b27,var(--red));padding:44px 4px 0}
.m-form .field{height:22px;font-size:11px;padding:3px 6px;margin-bottom:6px;border:1px solid #ddd}
.m-form .wide{height:55px}
.m-form .submit{display:inline-block;font-family:var(--serif);font-size:10px;text-transform:uppercase;color:var(--white);border:1px solid var(--white);padding:4px 14px;margin-left:6px;margin-top:10px}
.m-footer{height:1220px;background:var(--black);color:var(--white);padding:50px 6px 0}
.m-footer .brand{font-size:20px;width:170px;margin-left:2px}
.m-footer h4{font-family:var(--serif);font-weight:400;font-size:13px;text-transform:uppercase;margin:50px 0 18px}
.m-footer li{list-style:none;font-size:12px;line-height:2.55}
.m-footer .accent{color:var(--red);font-size:11px;display:block;margin-top:20px}
.m-footer .qc span{font-size:11.5px;line-height:1.5;display:block}
.m-footer .sub-field{width:200px;height:26px;font-size:11px;line-height:26px;border-radius:2px;margin-top:6px}
.m-footer .sub-btn{width:200px;height:26px;font-size:13px;line-height:26px;font-family:var(--serif);margin-top:8px}
.m-footer .socials{gap:8px;margin-top:30px}
.m-footer .socials i{width:20px;height:20px}
.m-footer .copy{font-size:10px;color:#999;line-height:1.5;margin-top:48px}
.m-footer .copy .accent{display:inline;font-size:10px;margin:0}
</style>
</head>
<body>

<div class="board-label label-desktop">Home Page</div>
<div class="board-label label-mobile">Mobile<br>Version</div>

<main class="desktop">
  <header class="d-nav">
    <div class="brand">Fernvale Quillstone Heritage</div>
    <nav class="d-menu"><span class="active">HOME</span><span>ABOUT</span><span>ADOPT</span><span>HORSES</span><span>DONATE / SHOP</span><span>CONTACT</span></nav>
  </header>

  <section class="d-hero" role="img" aria-label="Rider in a helmet seated on a dark bay horse inside a warmly lit indoor arena">
    <div class="d-hero-copy">
      <div class="l1">We Support</div>
      <div class="l2">And Develop</div>
      <p>Retired thoroughbred racehorses for their next chapter in life</p>
      <span class="btn">View Horses</span>
    </div>
  </section>

  <section class="d-intro">
    <div class="art" role="img" aria-label="Illustration of a white horse and a rider in a helmet beside a large red letter">
      <div class="tag">Retire.&nbsp; Retrain.&nbsp; Rehome.</div>
    </div>
    <p>Fernvale Quillstone Heritage Society (FQHS) is a registered<br>not-for-profit organization in Fernvale.</p>
  </section>

  <section class="d-what">
    <div class="copy">
      <h2>What is Thoroughbred<br>Aftercare?</h2>
      <p>The health, safety and welfare of our equine athletes does not end at the finish line, and retirement and aftercare are critical to the success of the racing industry.</p>
      <span class="btn">Learn More About Us</span>
    </div>
    <div class="circle" role="img" aria-label="Woman resting her head against a bay horse"></div>
  </section>

  <section class="d-adopt">
    <h2>Adopt a Horse</h2>
    <p>Fernvale Quillstone Heritage is committed to<br>helping match you with the perfect horse.</p>
    <div class="horse-row">
      <div class="photo" role="img" aria-label="Bay horse standing in a grassy paddock" style="background:var(--paddock)"></div>
      <div class="photo" role="img" aria-label="Dark bay horse standing in snow" style="background:var(--snow)"></div>
      <div class="photo" role="img" aria-label="Brown horse in a yellow flower field" style="background:var(--field)"></div>
    </div>
    <span class="btn">Adopt Now</span>
  </section>

  <section class="d-horses">
    <div class="photo" role="img" aria-label="Close portrait of a bay horse wearing a red halter"></div>
    <div class="card">
      <h3>Horses</h3>
      <p>Many desktop publishing packages and web page editors now use Lorem Ipsum as their default model text, and a search for 'lorem ipsum'</p>
      <span class="btn">More Ways To Give</span>
    </div>
  </section>

  <section class="d-contact">
    <h2>Have A Question Or Need More Information</h2>
    <div class="d-info">
      <div class="info-row">
        <svg width="22" height="22" viewBox="0 0 20 20"><circle cx="10" cy="10" r="9" fill="none" stroke="#fff" stroke-width="1.4"/><path d="M10 4.5a3.5 3.5 0 0 0-3.5 3.5c0 2.6 3.5 7 3.5 7s3.5-4.4 3.5-7A3.5 3.5 0 0 0 10 4.5z" fill="#fff"/><circle cx="10" cy="8" r="1.2" fill="#bd1f2d"/></svg>
        <div><b>LOCATION</b><span>Lorem Ipsum is simply<br>Dummy text P.O. Box 156</span></div>
      </div>
      <div class="info-row">
        <svg width="22" height="22" viewBox="0 0 20 20"><circle cx="10" cy="10" r="9" fill="none" stroke="#fff" stroke-width="1.4"/><path d="M7 5.5l2 2-1 1.5c.6 1.3 1.7 2.4 3 3l1.5-1 2 2-1.3 1.5C10 14.5 5.5 10 5.5 6.8z" fill="#fff"/></svg>
        <div><b>CALL US</b><span>123-456-789</span></div>
      </div>
      <div class="info-row">
        <svg width="22" height="22" viewBox="0 0 20 20"><circle cx="10" cy="10" r="9" fill="none" stroke="#fff" stroke-width="1.4"/><rect x="5.5" y="7" width="9" height="6.5" fill="#fff"/><path d="M5.5 7l4.5 3.5L14.5 7" fill="none" stroke="#bd1f2d" stroke-width="1"/></svg>
        <div><b>MAIL US</b><span>hello@fernvalemail.com</span></div>
      </div>
    </div>
    <div class="d-form">
      <div class="field">First Name</div><div class="field">Last Name</div>
      <div class="field">Phone</div><div class="field">Email</div>
      <div class="field wide">How can we help you?</div>
      <div class="foot"><div class="check"></div><div class="submit">SUBMIT NOW</div></div>
    </div>
  </section>

  <footer class="d-footer">
    <div class="brand">Fernvale Quillstone Heritage</div>
    <div class="d-col" style="left:253px"><h4>QUICK LINK</h4><ul><li>Home</li><li>About</li><li>Adopt</li><li>Horses</li><li>Donate / Shop</li><li>Contact</li></ul></div>
    <div class="d-col" style="left:385px"><h4>QUICK CONTACT</h4><ul><li class="accent">Location</li><li>Lorem Ipsum is simply</li><li>Dummy text P.O. Box 156</li><li class="accent">Location</li><li>Lorem Ipsum is simply</li><li>Dummy text P.O. Box 156</li></ul></div>
    <div class="d-col" style="left:541px"><h4>FOLLOW US</h4><div class="sub-field">Enter Your Mail ID</div><div class="sub-btn">Subscribe</div><div class="socials"><i></i><i></i><i></i><i></i></div></div>
    <div class="copy">Copyright 2021 <span class="accent">Fernvale</span> All Right Reserved</div>
  </footer>
</main>

<div class="closing">THANKS<br>FOR<br>WATCHING</div>

<main class="mobile">
  <header class="m-head">
    <div class="brand">Fernvale Quillstone Heritage</div>
    <svg width="16" height="12" viewBox="0 0 16 12"><rect width="16" height="2" fill="#1c1c1c"/><rect y="5" width="16" height="2" fill="#1c1c1c"/><rect y="10" width="16" height="2" fill="#1c1c1c"/></svg>
  </header>

  <section class="m-hero" role="img" aria-label="Rider on a dark bay horse inside a warmly lit indoor arena">
    <div class="m-hero-copy">
      We Support<br><span class="red">And Develop</span><br>retired thorough<br>bred racehorses<br>for their<br>next chapter in life<br>
      <span class="btn">View Horses</span>
    </div>
  </section>

  <section class="m-intro">
    <div class="art" role="img" aria-label="Illustration of a white horse and a rider beside a large red letter">
      <div class="tag">Retire.&nbsp; Retrain.&nbsp; Rehome.</div>
    </div>
    <p>Fernvale Quillstone Heritage Society (FQHS) is a registered not-for-profit organization in Fernvale.</p>
  </section>

  <section class="m-what">
    <div class="circle" role="img" aria-label="Woman resting her head against a bay horse"></div>
    <h2>What is<br>Thoroughbred<br>Aftercare?</h2>
    <p>The health, safety and welfare of our equine athletes does not end at the finish line, and retirement and aftercare are critical to the success of the racing industry.</p>
    <span class="btn">Learn More About Us</span>
  </section>

  <section class="m-adopt">
    <h2>Adopt a Horse</h2>
    <p>Fernvale Quillstone Heritage is committed to helping match you with the perfect horse.</p>
    <div class="slider">
      <div class="photo" role="img" aria-label="Dark bay horse standing in snow"></div>
      <span class="arrow prev"><svg width="24" height="24" viewBox="0 0 24 24"><path d="M14 7l-5 5 5 5" fill="none" stroke="#1c1c1c" stroke-width="2"/></svg></span>
      <span class="arrow next"><svg width="24" height="24" viewBox="0 0 24 24"><path d="M10 7l5 5-5 5" fill="none" stroke="#1c1c1c" stroke-width="2"/></svg></span>
    </div>
    <div class="center"><span class="btn">Adopt Now</span></div>
  </section>

  <section class="m-horses">
    <div class="photo" role="img" aria-label="Portrait of a bay horse wearing a red halter"></div>
    <div class="card">
      <h3>Horses</h3>
      <p>Many desktop publishing packages and web page editors now use Lorem Ipsum as their default model text, and a search for 'lorem ipsum'</p>
      <span class="btn">More Ways To Give</span>
    </div>
  </section>

  <section class="m-ask">
    <h2>Have A Question Or<br>Need More Information</h2>
    <div class="info-list">
      <div class="info-row">
        <svg width="22" height="22" viewBox="0 0 20 20"><circle cx="10" cy="10" r="9" fill="none" stroke="#fff" stroke-width="1.4"/><path d="M10 4.5a3.5 3.5 0 0 0-3.5 3.5c0 2.6 3.5 7 3.5 7s3.5-4.4 3.5-7A3.5 3.5 0 0 0 10 4.5z" fill="#fff"/><circle cx="10" cy="8" r="1.2" fill="#bd1f2d"/></svg>
        <div><b>LOCATION</b><span>Lorem Ipsum is simply<br>Dummy text P.O. Box 156</span></div>
      </div>
      <div class="info-row">
        <svg width="22" height="22" viewBox="0 0 20 20"><circle cx="10" cy="10" r="9" fill="none" stroke="#fff" stroke-width="1.4"/><path d="M7 5.5l2 2-1 1.5c.6 1.3 1.7 2.4 3 3l1.5-1 2 2-1.3 1.5C10 14.5 5.5 10 5.5 6.8z" fill="#fff"/></svg>
        <div><b>CALL US</b><span>123-456-789</span></div>
      </div>
      <div class="info-row">
        <svg width="22" height="22" viewBox="0 0 20 20"><circle cx="10" cy="10" r="9" fill="none" stroke="#fff" stroke-width="1.4"/><rect x="5.5" y="7" width="9" height="6.5" fill="#fff"/><path d="M5.5 7l4.5 3.5L14.5 7" fill="none" stroke="#bd1f2d" stroke-width="1"/></svg>
        <div><b>MAIL US</b><span>hello@fernvalemail.com</span></div>
      </div>
    </div>
  </section>

  <section class="m-form">
    <div class="field">First Name</div>
    <div class="field">Last Name</div>
    <div class="field">Phone</div>
    <div class="field">Email</div>
    <div class="field wide">How can we help&nbsp; you?</div>
    <span class="submit">Submit Now</span>
  </section>

  <footer class="m-footer">
    <div class="brand">Fernvale<br>Quillstone<br>Heritage</div>
    <h4>Quick Link</h4>
    <ul><li>Home</li><li>About</li><li>Adopt</li><li>Horses</li><li>Donate / Shop</li><li>Contact</li></ul>
    <h4>Quick Contact</h4>
    <div class="qc">
      <span class="accent">Location</span><span>Lorem Ipsum is simply<br>Dummy text<br>P.O. Box 156</span>
      <span class="accent">Location</span><span>Lorem Ipsum is simply<br>Dummy text<br>P.O. Box 156</span>
    </div>
    <h4>Follow Us</h4>
    <div class="sub-field">Enter Your Mail ID</div>
    <div class="sub-btn">Subscribe</div>
    <div class="socials"><i></i><i></i><i></i><i></i></div>
    <div class="copy">Copyright 2021 <span class="accent">Fernvale</span><br>All Right Reserved</div>
  </footer>
</main>

</body>
</html>
```